first fantastic look and impression

We are looking for a concept for letterhead, business card, emailfooter and template for invoices or offers for our company in the consultation business.
The dancer is a symbol who we are: it looks simple, but there is a lot of hard work and many years of training in this movement. The look is also what we want: elegant, modern, strong, with a touch of extravaganza
Target Market(s)
Hotelbusiness , Consulting
Font styles to use
Sans Serif
Other font styles liked:
- please give us a option we are open
Requirements
Must have
- We are not typical consultants but sparring partners and coaches for the hotel and that should also be expressed in the design. Maybe there is an icon that supports the whole thing. We are more modern and bolder than our industry colleagues.
we are modern, fresh, agile, fast
Nice to have
- a icon

```html
<!DOCTYPE html>
<html lang="en">
<head>
<meta charset="utf-8">
<title>Halvorn – Business Card</title>
<link rel="stylesheet" href="https://fonts.googleapis.com/css2?family=Raleway:wght@500;700&family=Roboto:wght@400&display=swap">
<style>
  :root {
    --backdrop: #d3d6d7;
    --paper: #f1f0ec;
    --ink: #141414;
    --ink-soft: #2b2b2b;
    --night: #0d0f1d;
    --silver: #d9dadc;
  }
  * { margin: 0; padding: 0; box-sizing: border-box; }
  html, body { width: 1200px; height: 1050px; overflow: hidden; }
  body { background: var(--backdrop); position: relative; }

  .card {
    position: absolute;
    width: 540px;
    height: 310px;
    border-radius: 3px;
  }

  /* Front */
  .card--front {
    left: 60px;
    top: 520px;
    background: var(--paper);
    color: var(--ink);
    display: flex;
    align-items: center;
    padding: 0 34px 0 40px;
  }
  .brand {
    display: flex;
    align-items: center;
    gap: 10px;
    width: 210px;
  }
  .brand__mark {
    width: 12px;
    height: 12px;
    background: var(--ink);
    flex: none;
  }
  .brand__name {
    font-family: "Raleway", sans-serif;
    font-weight: 500;
    font-size: 30px;
    letter-spacing: 3px;
    text-transform: uppercase;
    color: var(--ink);
  }
  .divider {
    width: 2px;
    height: 190px;
    margin: 0 26px 0 8px;
    display: flex;
    flex-direction: column;
    justify-content: space-between;
  }
  .divider span { display: block; width: 2px; background: var(--ink); }
  .divider span:first-child { height: 26px; }
  .divider span:last-child { height: 144px; }

  .contact { font-family: "Roboto", sans-serif; color: var(--ink-soft); }
  .contact__name {
    font-family: "Raleway", sans-serif;
    font-weight: 700;
    font-size: 17px;
    letter-spacing: 0.5px;
    text-transform: uppercase;
    color: var(--ink);
  }
  .contact__role {
    font-family: "Raleway", sans-serif;
    font-weight: 700;
    font-size: 14px;
    color: var(--ink-soft);
    margin-bottom: 12px;
  }
  .contact__address { font-size: 14px; line-height: 1.3; margin-bottom: 6px; }
  .contact__list { list-style: none; font-size: 14px; line-height: 1.45; }
  .contact__list li { display: flex; align-items: center; gap: 8px; }
  .contact__list svg { width: 13px; height: 13px; flex: none; }

  /* Back */
  .card--back {
    left: 640px;
    top: 200px;
    background: var(--night);
    display: flex;
    align-items: center;
    justify-content: center;
    gap: 16px;
  }
  .card--back .brand__mark { width: 18px; height: 18px; background: var(--silver); }
  .card--back .brand__name { font-size: 50px; letter-spacing: 6px; color: var(--silver); }
</style>
</head>
<body>

  <section class="card card--back" aria-label="Business card, back">
    <span class="brand__mark"></span>
    <span class="brand__name">Halvorn</span>
  </section>

  <section class="card card--front" aria-label="Business card, front">
    <div class="brand">
      <span class="brand__mark"></span>
      <span class="brand__name">Halvorn</span>
    </div>
    <div class="divider"><span></span><span></span></div>
    <div class="contact">
      <p class="contact__name">Elias Marwood</p>
      <p class="contact__role">Managing Director</p>
      <p class="contact__address">48 Larch Crescent,<br>Maple Bay, ON K2B 7T4</p>
      <ul class="contact__list">
        <li>
          <svg viewBox="0 0 24 24" aria-hidden="true"><path fill="currentColor" d="M6.6 10.8a15.1 15.1 0 0 0 6.6 6.6l2.2-2.2a1 1 0 0 1 1-.25 11.4 11.4 0 0 0 3.6.57 1 1 0 0 1 1 1V20a1 1 0 0 1-1 1A17 17 0 0 1 3 4a1 1 0 0 1 1-1h3.5a1 1 0 0 1 1 1c0 1.25.2 2.45.57 3.57a1 1 0 0 1-.25 1z"/></svg>
          +15550142873
        </li>
        <li>
          <svg viewBox="0 0 24 24" aria-hidden="true"><rect x="2" y="5" width="20" height="14" fill="currentColor"/><path d="M2 5l10 8 10-8" fill="none" stroke="#f1f0ec" stroke-width="1.6"/></svg>
          hello@halvorn.com
        </li>
        <li>
          <svg viewBox="0 0 24 24" aria-hidden="true" fill="none" stroke="currentColor" stroke-width="2"><circle cx="12" cy="12" r="10"/><path d="M2 12h20M12 2c3 3 3 17 0 20M12 2c-3 3-3 17 0 20"/></svg>
          www.halvorn.com
        </li>
      </ul>
    </div>
  </section>

</body>
</html>
```